40k Ultra High Pressure Waterblasing Ad

We need 1 page flyer ad for our industry's brochure/membership directory.
We're a manufacturer & supplier for the Ultra High Pressure Waterblasting industry.
We'd like the ad to be simple and clean, highlighting some of our parts. Our dedication to our customers and affordable prices.
Some of the parts are Dorwell Maxtrane Hoses, Sapphire Nozzles, Rotating Jetlance.

Our website is brimstreamco.com

Requirements
Must have
• Dorwell Maxtrane 40k Hose
• Sapphire Nozzles
• Rotating Jetlance
• **Update - Would like to incorporate the "storm sleeve logo w/ bulldog" from uploaded dorwell storm sleeve hose attachment. Highlighting the hose's features.
Nice to have
• Brief Bullet points or something else highlighting what we sell.
• - Pump replacement parts
• - Sapphire Nozzles
• - Rotating Jetlance
• - Fittings and adapters
• - Safety Gear
• I've uploaded past ads we've used.
Should not have
• Lots of text area

```html
<!DOCTYPE html>
<html lang="en">
<head>
<meta charset="utf-8">
<title>Brimstream Technologies – UHP Flyer</title>
<link href="https://fonts.googleapis.com/css2?family=Arimo:ital,wght@0,400;0,700;1,400&display=swap" rel="stylesheet">
<style>
  :root{
    --page-bg:#cfcccc;
    --blue:#1a73bd;
    --blue-deep:#0d4f8e;
    --navy:#1b2f6b;
    --ring:#1f7fcb;
    --halo:#e4f1fa;
    --white:#ffffff;
    --ink:#1c1c1c;
    --grey:#8a8a8a;
  }
  *{margin:0;padding:0;box-sizing:border-box}
  html,body{width:1200px;height:2400px;overflow:hidden;background:var(--page-bg);font-family:"Arimo",Arial,sans-serif}
  .flyer{position:absolute;left:0;top:425px;width:1200px;height:1550px;background:var(--white);overflow:hidden}
  .flyer-shapes{position:absolute;inset:0}
  .headline{position:absolute;left:102px;top:92px;color:var(--white);font-weight:700;font-size:40px;line-height:56px;letter-spacing:2px;text-transform:uppercase;white-space:nowrap}
  .brand{position:absolute;left:19px;top:400px;width:540px;text-align:center}
  .brand-mark{display:inline-block;width:120px;height:120px;border-radius:50%;background:var(--navy);margin-bottom:50px}
  .brand-name{color:var(--navy);font-weight:700;font-size:38px;line-height:48px}
  .contact{position:absolute;left:19px;top:730px;width:540px;text-align:center;color:var(--ink)}
  .contact-email,.contact-web{font-size:31px;line-height:44px}
  .contact-phone{font-size:42px;font-weight:700;color:var(--blue);line-height:50px}
  .prices-title{position:absolute;left:102px;top:958px;color:var(--white);font-weight:700;font-size:30px;letter-spacing:1.5px;white-space:nowrap}
  .product-list{position:absolute;left:102px;top:1025px;list-style:none;color:var(--white);font-weight:700;font-size:33px}
  .product-list li{height:52px;display:flex;align-items:center;gap:20px;white-space:nowrap}
  .product-list li::before{content:"";width:0;height:0;border-left:13px solid var(--white);border-top:9px solid transparent;border-bottom:9px solid transparent}
  .badge-family{position:absolute;left:574px;top:966px;width:224px;text-align:center;color:var(--ink);font-weight:700;font-size:32px;line-height:40px}
  .badge-usa{position:absolute;left:574px;top:1140px;width:224px;text-align:center;color:var(--white);font-weight:700}
  .badge-usa .small{font-size:24px;display:block}
  .badge-usa .big{font-size:54px;display:block;line-height:56px}
  .badge-usa .stars{font-size:16px;letter-spacing:8px;display:block}
  .partner{position:absolute;top:1380px;height:84px;display:flex;align-items:center;justify-content:center;gap:12px;font-weight:700;color:var(--ink);border:4px solid var(--ink);background:var(--white);white-space:nowrap}
  .partner-dorwell{left:98px;width:240px;font-size:36px}
  .partner-storm{left:364px;width:270px;font-size:26px}
  .partner-storm .square{width:30px;height:30px;background:var(--grey)}
  .tagline{position:absolute;left:666px;top:1380px;width:433px;height:84px;display:flex;align-items:center;justify-content:center;font-style:italic;font-size:29px;color:var(--ink);border-top:3px solid var(--grey);border-bottom:5px solid var(--grey);white-space:nowrap}
</style>
</head>
<body>
<main class="flyer">
  <svg class="flyer-shapes" width="1200" height="1550" viewBox="0 0 1200 1550">
    <defs>
      <linearGradient id="band" x1="0" x2="1">
        <stop offset="0" stop-color="#1565ad"/>
        <stop offset="1" stop-color="#2f95da"/>
      </linearGradient>
      <radialGradient id="haloFill" cx="0.5" cy="0.5" r="0.5">
        <stop offset="0.7" stop-color="#d6eaf8"/>
        <stop offset="1" stop-color="#eef6fc"/>
      </radialGradient>
      <radialGradient id="lanceFill" cx="0.5" cy="0.45" r="0.6">
        <stop offset="0" stop-color="#c9ccd1"/>
        <stop offset="0.45" stop-color="#eef5fa"/>
        <stop offset="1" stop-color="#a9d2ee"/>
      </radialGradient>
      <radialGradient id="nozzleFill" cx="0.5" cy="0.5" r="0.6">
        <stop offset="0" stop-color="#9c9286"/>
        <stop offset="0.4" stop-color="#e9eef2"/>
        <stop offset="1" stop-color="#a9d2ee"/>
      </radialGradient>
      <radialGradient id="hoseFill" cx="0.45" cy="0.45" r="0.6">
        <stop offset="0" stop-color="#4a4d52"/>
        <stop offset="0.55" stop-color="#8d9298"/>
        <stop offset="1" stop-color="#cfe5f4"/>
      </radialGradient>
    </defs>
    <!-- halos -->
    <circle cx="961" cy="426" r="300" fill="url(#haloFill)"/>
    <circle cx="748" cy="656" r="262" fill="url(#haloFill)"/>
    <circle cx="1109" cy="1050" r="380" fill="url(#haloFill)"/>
    <!-- top band -->
    <path d="M0 0H1200V60Q900 110 760 230Q700 280 660 295H0Z" fill="url(#band)"/>
    <!-- lower band -->
    <rect x="0" y="941" width="1200" height="364" fill="url(#band)"/>
    <rect x="0" y="948" width="567" height="59" fill="var(--blue-deep)"/>
    <!-- product photos -->
    <g role="img" aria-label="Photo of a rotating jetlance tool">
      <circle cx="961" cy="426" r="223" fill="var(--ring)"/>
      <circle cx="961" cy="426" r="203" fill="url(#lanceFill)"/>
    </g>
    <g role="img" aria-label="Photo of a row of sapphire nozzles">
      <circle cx="748" cy="656" r="213" fill="var(--ring)"/>
      <circle cx="748" cy="656" r="195" fill="url(#nozzleFill)"/>
    </g>
    <g role="img" aria-label="Photo of a coiled high pressure hose">
      <circle cx="1109" cy="1050" r="312" fill="var(--ring)"/>
      <circle cx="1109" cy="1050" r="292" fill="url(#hoseFill)"/>
    </g>
    <!-- badge -->
    <path d="M567 925H804V1250L685 1312L567 1250Z" fill="var(--blue-deep)"/>
    <rect x="574" y="932" width="223" height="183" fill="var(--white)"/>
    <path d="M584 1125H787V1238L685 1288L584 1238Z" fill="var(--blue)" stroke="var(--white)" stroke-width="4"/>
    <!-- bottom strip -->
    <rect x="0" y="1528" width="1200" height="22" fill="var(--blue)"/>
  </svg>

  <h1 class="headline">Supplying the essentials<br>in the UHP surface<br>preparation industry</h1>

  <div class="brand">
    <span class="brand-mark"></span>
    <div class="brand-name">Brimstream<br>Technologies Inc.</div>
  </div>

  <div class="contact">
    <p class="contact-email">Email: info@brimstreamco.com</p>
    <p class="contact-phone">Call: 555-014-2290</p>
    <p class="contact-web">www.brimstreamco.com</p>
  </div>

  <h2 class="prices-title">AT AFFORDABLE PRICES</h2>
  <ul class="product-list">
    <li>Pump replacement parts</li>
    <li>Sapphire Nozzles</li>
    <li>Rotating Jetlance</li>
    <li>Fittings and adapters</li>
    <li>Safety Gear</li>
  </ul>

  <p class="badge-family">Family<br>Owned and<br>Operated</p>
  <p class="badge-usa"><span class="small">MADE IN</span><span class="big">USA</span><span class="stars">★★★</span></p>

  <div class="partner partner-dorwell">Dorwell</div>
  <div class="partner partner-storm">STORM SLEEVE<span class="square"></span></div>
  <p class="tagline">“Our Customers Come First”</p>
</main>
</body>
</html>
```